Unique Business Card Design

Unique Business Card design for our orthotic and prosthetic company. Our logo is on our website, color is light blue. Unique shape (artificial leg shaped, vertical, etc..) preferred. Logo, business name, individual name and basic demographics needed.

Industry/Entity Type

Business

Contact Information for Business Card

Logo, Industry, Phone # Logo, "Prosthetic & Orthotic Services" Place to add individual name and contact info

Colors
cee9f5

Requirements
Must have
• The icon must be there, placement of "Prosthetic & Orthotic Services" can be moved
Nice to have
• Like the mix of light blue, and a little darker blue. One design included the icons from my website which was a nice touch

```html
<!DOCTYPE html>
<html lang="en">
<head>
<meta charset="utf-8">
<title>Stridewell Inc. Business Card</title>
<link rel="stylesheet" href="https://fonts.googleapis.com/css2?family=Arimo:wght@400;700&display=swap">
<style>
  :root {
    --backdrop: #3b3531;
    --card: #151617;
    --card-back: #111213;
    --blue: #2f7fd3;
    --text-light: #e4e4e4;
    --rule: #8a8a8a;
    --emboss: #2a2b2d;
  }
  * { box-sizing: border-box; margin: 0; padding: 0; }
  html, body {
    width: 1200px; height: 864px; overflow: hidden;
    background: var(--backdrop);
    font-family: "Arimo", Arial, sans-serif;
  }
  .stage { position: relative; width: 1200px; height: 864px; }
  .card {
    position: absolute; top: 283px;
    width: 520px; height: 297px;
    border-radius: 3px;
    overflow: hidden;
    box-shadow: 0 10px 24px rgba(0,0,0,.45);
  }
  /* back */
  .card-back { left: 50px; background: var(--card-back); }
  .back-mark {
    position: absolute; left: 200px; top: 52px;
    width: 120px; height: 120px; border-radius: 50%;
    background: radial-gradient(circle at 40% 35%, #3a3b3e, var(--emboss));
  }
  .back-footer {
    position: absolute; left: 40px; right: 40px; top: 208px;
    display: flex; align-items: center; gap: 14px;
    color: #bdbdbd; font-size: 12px; letter-spacing: .3px;
  }
  .back-footer .rule { flex: 1; height: 1px; background: #555; }
  /* front */
  .card-front { left: 630px; background: var(--card); color: var(--text-light); }
  .brand {
    position: absolute; right: 30px; top: 24px;
    display: flex; align-items: center; gap: 10px;
    white-space: nowrap;
  }
  .brand-dot { width: 52px; height: 52px; border-radius: 50%; background: var(--blue); flex: none; }
  .brand-text { display: flex; flex-direction: column; align-items: stretch; }
  .brand-name {
    color: var(--blue); font-weight: 700; font-size: 17px; letter-spacing: .4px;
    border-bottom: 2px solid var(--blue); padding-bottom: 2px;
  }
  .brand-tagline { color: var(--blue); font-size: 10px; margin-top: 4px; }
  .person {
    position: absolute; left: 32px; top: 60px;
    color: var(--blue); font-size: 18px; white-space: nowrap;
  }
  .person .credentials { font-size: 11px; margin-left: 4px; }
  .divider {
    position: absolute; left: 32px; right: 30px; top: 94px;
    height: 1px; background: var(--rule);
  }
  .contacts {
    position: absolute; left: 32px; top: 108px;
    list-style: none; font-size: 12.5px; line-height: 20px;
  }
  .contacts li { display: flex; align-items: center; gap: 8px; }
  .contacts svg { width: 12px; height: 12px; fill: var(--blue); flex: none; }
  .address {
    position: absolute; right: 30px; bottom: 26px;
    text-align: right; font-size: 13px; line-height: 19px; font-style: normal;
  }
</style>
</head>
<body>
<main class="stage">
  <section class="card card-back" aria-label="Card back">
    <div class="back-mark" role="img" aria-label="Embossed company emblem area"></div>
    <div class="back-footer">
      <span class="rule"></span>
      <span class="website">www.stridewellinc.com</span>
      <span class="rule"></span>
    </div>
  </section>

  <section class="card card-front" aria-label="Card front">
    <div class="brand">
      <span class="brand-dot"></span>
      <div class="brand-text">
        <span class="brand-name">STRIDEWELL INC.</span>
        <span class="brand-tagline">Prosthetic &amp; Orthotic Services</span>
      </div>
    </div>

    <p class="person">Mirela Oskanian,<span class="credentials">CO LPO</span></p>
    <div class="divider"></div>

    <ul class="contacts">
      <li>
        <svg viewBox="0 0 24 24"><path d="M6.6 10.8a15.1 15.1 0 0 0 6.6 6.6l2.2-2.2a1 1 0 0 1 1-.25 11.4 11.4 0 0 0 3.6.57 1 1 0 0 1 1 1V20a1 1 0 0 1-1 1A17 17 0 0 1 3 4a1 1 0 0 1 1-1h3.5a1 1 0 0 1 1 1c0 1.25.2 2.45.57 3.57a1 1 0 0 1-.25 1z"/></svg>
        555.201.4400
      </li>
      <li>
        <svg viewBox="0 0 24 24"><path d="M7 1h10a2 2 0 0 1 2 2v18a2 2 0 0 1-2 2H7a2 2 0 0 1-2-2V3a2 2 0 0 1 2-2zm0 3v14h10V4z"/></svg>
        555.201.4418
      </li>
      <li>
        <svg viewBox="0 0 24 24"><path d="M6 2h9l3 3v4h2a2 2 0 0 1 2 2v9a2 2 0 0 1-2 2H4a2 2 0 0 1-2-2v-9a2 2 0 0 1 2-2h2zm2 2v5h8V6h-2V4zm-2 9v2h3v-2zm5 0v2h3v-2z"/></svg>
        555-3307126
      </li>
      <li>
        <svg viewBox="0 0 24 24"><path d="M2 5h20v14H2zm2 2v.5l8 5 8-5V7l-8 5z"/></svg>
        moskanian@stridewellinc.com
      </li>
    </ul>

    <address class="address">
      2260 W. 14th St.<br>
      Lakeview, NY 11390<br>
      www.stridewellinc.com
    </address>
  </section>
</main>
</body>
</html>
```